New Fun, Positive, energised looking Business Card Needed for High Achiever Coach

I am looking for a two sided full colour business card. I am self employed and have recently re branded my 1-2-1 work re-vitalising high achievers. My target client base for these cards is therefore high achievers - usually aged 40 -55, they are often entrepreneurs, CEO or work in banking and finance and 2/3 are male. I work with them on 90 day or 6 month coaching programs to help them live their success in a healthier, more sustainable and fulfiiled way. They pay for this privately so though they are corporate types the cards need not look 'corporate'. I want to portray the idea of transformation, vitality and re-connecting.
You can get a feel for the look I like on my new website: morvenlisk.co.uk
I want to use this logo with strapline (Re-Vitalising High Achievers) (I purchased off Logoharbor) and font/ colours (the turquoise and green).
Details to include on the card:
www.morvenlisk.co.uk
+44 7915 302618
morven@morvenlisk.co.uk
skype: morvenlisk
I'd also like to include:
Do you struggle to switch off? Want to be healthier and feel fitter? Want closer relationships? More clarity over the direction you are headed? I can help you do these things using integrated mind-body techniques. Visit morvenlisk.co.uk TODAY to apply for a FREE Breakthrough session.
BUT if that is too much text for a card I am open to advice/ammendments.
Updates
Thanks for your design - I am considering them. PLease change the wording to :

```html
<!DOCTYPE html>
<html lang="en">
<head>
<meta charset="utf-8">
<title>Morven Lisk – Business Card</title>
<link rel="stylesheet" href="https://fonts.googleapis.com/css2?family=Open+Sans:wght@400;700&family=Satisfy&display=swap">
<style>
  :root {
    --turquoise: #1ea7cf;
    --green: #5bb863;
    --white: #ffffff;
    --ink: #ffffff;
    --backdrop: #eceeef;
  }
  * { box-sizing: border-box; margin: 0; padding: 0; }
  html, body {
    width: 1200px; height: 720px; overflow: hidden;
    background: var(--backdrop);
    font-family: "Open Sans", Arial, sans-serif;
  }
  .canvas {
    position: relative; width: 1200px; height: 720px;
    display: flex; align-items: center; justify-content: center; gap: 40px;
  }
  .card {
    position: relative; width: 540px; height: 330px; overflow: hidden;
    box-shadow: 0 6px 18px rgba(0,0,0,0.12);
  }
  .card-front { background: var(--white); }
  .front-wave { position: absolute; inset: 0; width: 540px; height: 330px; }
  .brand {
    position: absolute; left: 36px; top: 84px;
  }
  .brand-line { display: flex; align-items: center; gap: 10px; }
  .brand-dot {
    width: 28px; height: 28px; border-radius: 50%; background: var(--green);
  }
  .brand-name {
    font-weight: 700; font-size: 30px; line-height: 40px;
    color: var(--turquoise); letter-spacing: 0.3px;
  }
  .strapline {
    margin-top: 2px;
    font-family: "Satisfy", "Brush Script MT", cursive;
    font-size: 18px; line-height: 22px; color: var(--turquoise);
  }
  .contact-list {
    position: absolute; left: 342px; top: 128px; list-style: none;
    color: var(--ink); font-size: 13px; line-height: 23px;
  }
  .contact-list li { display: flex; align-items: center; gap: 7px; }
  .contact-list .handle { padding-left: 64px; }
  .contact-icon { width: 13px; height: 13px; flex: none; }
  .card-back {
    background: var(--turquoise); color: var(--ink);
    display: flex; flex-direction: column; align-items: center; justify-content: center;
    text-align: center; font-size: 17px; line-height: 24px; padding: 0 36px;
  }
  .card-back p + p { margin-top: 14px; }
  .card-back strong { font-weight: 700; }
</style>
</head>
<body>
<main class="canvas">
  <section class="card card-front" aria-label="Card front">
    <svg class="front-wave" viewBox="0 0 540 330" aria-hidden="true">
      <path fill="var(--green)" d="M0,291 C180,286 250,136 330,98 C400,68 480,66 540,64 L540,330 L0,330 Z"/>
      <path fill="var(--white)" d="M0,299 C180,294 250,144 330,106 C400,76 480,74 540,72 L540,330 L0,330 Z"/>
      <path fill="var(--turquoise)" d="M0,305 C180,300 250,150 330,112 C400,82 480,80 540,78 L540,330 L0,330 Z"/>
      <path fill="none" stroke="var(--white)" stroke-width="1.6" d="M0,316 C180,311 252,163 332,124 C402,95 480,93 540,91"/>
    </svg>
    <div class="brand">
      <div class="brand-line">
        <span class="brand-dot"></span>
        <span class="brand-name">Morven Lisk</span>
      </div>
      <p class="strapline">Re-Vitalising High Achievers</p>
    </div>
    <ul class="contact-list">
      <li>
        <svg class="contact-icon" viewBox="0 0 16 16" aria-hidden="true"><circle cx="8" cy="8" r="7" fill="none" stroke="currentColor" stroke-width="1.4"/><path d="M5.5 4.5l1.5 1.5-1 1c.6 1.3 1.7 2.4 3 3l1-1 1.5 1.5-1.2 1.2C7.5 12 4 8.5 4.3 5.7z" fill="currentColor"/></svg>
        +44 7915 302618
      </li>
      <li>
        <svg class="contact-icon" viewBox="0 0 16 16" aria-hidden="true"><circle cx="8" cy="8" r="7.5" fill="currentColor"/><rect x="4" y="5.5" width="8" height="5.5" fill="var(--turquoise)"/><path d="M4 5.5l4 3 4-3" fill="none" stroke="currentColor" stroke-width="1"/></svg>
        morven@morvenlisk.co.uk
      </li>
      <li>
        <svg class="contact-icon" viewBox="0 0 16 16" aria-hidden="true"><circle cx="8" cy="8" r="7" fill="none" stroke="currentColor" stroke-width="1.4"/><ellipse cx="8" cy="8" rx="3" ry="7" fill="none" stroke="currentColor" stroke-width="1"/><path d="M1 8h14" stroke="currentColor" stroke-width="1"/></svg>
        www.morvenlisk.co.uk
      </li>
      <li class="handle">
        <svg class="contact-icon" viewBox="0 0 16 16" aria-hidden="true"><circle cx="8" cy="8" r="7" fill="currentColor"/></svg>
        morvenlisk
      </li>
    </ul>
  </section>

  <section class="card card-back" aria-label="Card back">
    <p>Do you struggle to switch off?<br>Want to be healthier and feel fitter?<br>Want closer relationships?<br>More clarity over the direction you are headed?</p>
    <p>I can help you do these things using integrated<br>mind-body techniques.</p>
    <p>Visit <strong>morvenlisk.co.uk</strong> TODAY to apply for a<br>FREE Breakthrough session.</p>
  </section>
</main>
</body>
</html>
```